Ashmoor Web Design Project

I need the front page and an internal page designed for this client's website. The logo is attached. Obviously the colors have to go with and/or work with the logo colors. I also attached a very rough brochure layout to help you see the direction we're going in with print materials. The rough site map is also attached. I see a slider on the homepage, the art for which I may come back to you to create. This clinic is in a very high end Dallas neighborhood. The hook is that it's a primary care and urgent facility with convenient hours.

I don't know how much this impacts your design, but this will be a Wordpress site and I'm using a framework called Brovila (brovila.com). If Brovila proves to be inflexible, I'll have to get a template that allows me to execute your design.

This site (http://lanternvaleclinic.com) has the type and quality of content I will eventually have on the Ashmoor site.

I just revised the brief for this project. I added the site map and added details to the overview and the "Must Have" section. Thank you for revisiting the brief. 

Reason: Christmas was a bad time to end it.

Target Market(s)

Women 25-54 with children living at home, income over $150k/year

Industry/Entity Type

Clinic

Requirements
Must have
• Masthead incorporating the logo
Followed by the primary nav
Slider on the home page below that
Dual nav - 1 with the nav in the attached site map
2 secondary nav with areas of healthcare
There will three blocks under the nav
1. It's about time (with a small blurb less than 50 words.
2. It's about choices (with small blurb)
3. It's about you (with small blurb)
Three footer blocks
patient check in link on every page
"No appointment? No problem" icon on every page

```html
<!DOCTYPE html>
<html lang="en">
<head>
<meta charset="utf-8">
<title>Ashmoor Medical</title>
<link href="https://fonts.googleapis.com/css2?family=Open+Sans:wght@400;600;700&family=PT+Sans:wght@400;700&display=swap" rel="stylesheet">
<style>
:root{
  --green:#1aa84f;
  --blue:#1a6aa8;
  --link:#2a6fb3;
  --text:#555;
  --dark:#333;
  --panel:#f3f3f3;
}
*{margin:0;padding:0;box-sizing:border-box}
html,body{width:800px;height:1200px;overflow:hidden}
body{position:relative;font-family:"Open Sans",Arial,sans-serif;color:var(--text);background:#fff}
.abs{position:absolute}
.sky{left:0;top:29px;width:800px;height:430px;background:linear-gradient(180deg,#76acdc 0%,#a9cdec 45%,#e9f2fa 80%,#fff 100%)}
.topbar{left:0;top:0;width:800px;height:29px;background:var(--green)}
.social{top:6px;width:18px;height:18px;border-radius:50%;background:#fff}
.toplinks{right:80px;top:10px;font-size:7px;color:#fff;letter-spacing:.2px}
.toplinks span{margin-left:10px}
.brand{left:88px;top:66px;display:flex;align-items:center;gap:5px}
.brand-mark{width:24px;height:24px;border-radius:50%;background:var(--blue)}
.brand-name{font-family:"PT Sans",sans-serif;font-weight:700;font-size:18px;color:var(--blue)}
.tagline{left:118px;top:86px;font-size:5.5px;color:var(--blue)}
.contact{left:592px;top:71px;font-family:"PT Sans",sans-serif;font-size:13px;color:#555;line-height:17px;white-space:pre}
.mainnav{left:80px;top:110px;width:640px;height:38px;background:var(--green)}
.mainnav span{position:absolute;top:14px;transform:translateX(-50%);font-size:9px;font-weight:700;color:#fff}
.search{left:558px;top:122px;width:152px;height:15px;border-radius:8px;background:#fff;font-size:6px;color:#999;padding:3px 6px}
.slider{left:80px;top:148px;width:640px;height:278px;background:linear-gradient(135deg,#e8e2d8 0%,#d9c3a6 40%,#c6a17d 65%,#ebe7e1 100%)}
.dot{top:157px;width:10px;height:10px;border-radius:50%;background:#fff;border:1px solid #ccc}
.dot.on{background:var(--blue)}
.slide-title{left:98px;top:349px;font-family:"PT Sans",sans-serif;font-weight:700;font-size:25px;line-height:28px;color:#fff;text-shadow:0 1px 3px rgba(0,0,0,.35)}
.appt{left:526px;top:156px;width:182px;height:260px;background:rgba(245,245,245,.93)}
.appt h3{position:absolute;left:0;right:0;top:8px;text-align:center;font-family:"PT Sans",sans-serif;font-weight:700;font-size:12px;color:var(--green)}
.field{left:536px;width:164px;height:19px;background:#fff;border:1px solid #e1e1e1;font-size:6px;color:#555;padding:5px 5px}
.label{left:535px;font-size:6px;color:#555}
.radio{display:inline-block;width:6px;height:6px;border:1px solid #888;border-radius:50%;vertical-align:middle;margin-right:3px}
.captcha{left:540px;top:379px;width:48px;height:12px;background:#2e3a46;color:#fff;font-size:6px;letter-spacing:3px;padding:2px 8px}
.submit{left:587px;top:398px;width:60px;height:16px;background:var(--green);color:#fff;font-size:7px;text-align:center;line-height:16px}
.shadow{left:80px;top:426px;width:640px;height:14px;background:radial-gradient(ellipse at top,rgba(0,0,0,.18),rgba(0,0,0,0) 70%)}
.heading{font-family:"PT Sans",sans-serif;font-weight:400;font-size:14.5px;color:var(--blue);text-transform:uppercase}
.cat{left:88px;width:144px;height:26px;border-bottom:1px dotted #bbb;font-size:6.5px;color:#444}
.cat span{position:absolute;left:21px;top:9px}
.cat i,.sub i{position:absolute;left:0;top:9px;font-style:normal;font-size:7px;color:#666}
.more{width:0;height:0;border-left:7px solid transparent;border-right:7px solid transparent;border-top:7px solid #666}
.photo{background:linear-gradient(135deg,#eef0f1,#d8c7b3 55%,#f5f5f5)}
.para{font-size:6.5px;line-height:9.6px;color:#555;text-align:justify}
.learn{font-size:6.5px;color:var(--green);text-decoration:underline}
.svc{left:82px;width:152px;height:26px;background:var(--panel);border:1px solid #e4e4e4;font-size:6.5px;color:#444;padding:8px 7px}
.svc b{position:absolute;right:14px;top:7px;font-size:8px;color:#555}
.sub{left:95px;width:139px;height:26px;border-bottom:1px dotted #bbb;font-size:6.5px;color:#444}
.sub span{position:absolute;left:13px;top:9px}
.treat-img{top:744px;width:124px;height:54px}
.treat h4{font-family:"PT Sans",sans-serif;font-weight:700;font-size:11.5px;color:#333;margin:16px 0 7px}
.treat ul{list-style:none}
.treat li{font-size:6.5px;color:var(--link);height:20px}
.badge{left:88px;top:1056px;width:128px;height:64px;border-radius:10px;background:#dbe6f3}
.arrowbtn{top:1024px;width:11px;height:11px;border:1px solid #999;font-size:6px;text-align:center;line-height:9px;color:#444}
.avatar{width:36px;height:33px;background:linear-gradient(#ddd,#9a9a9a)}
.quote{font-size:6.5px;line-height:10px;color:#444;width:180px}
.who{font-size:6.5px;line-height:10px;color:#444}
.footer{left:0;top:1158px;width:800px;height:42px;background:var(--green)}
.copy{left:78px;top:1176px;font-size:6.5px;color:#fff}
.flink{top:1176px;font-size:6.5px;color:#fff}
</style>
</head>
<body>
<div class="abs sky"></div>

<header>
  <div class="abs topbar"></div>
  <div class="abs social" style="left:83px"></div>
  <div class="abs social" style="left:105px"></div>
  <div class="abs social" style="left:127px"></div>
  <div class="abs toplinks"><span>REGISTER</span><span>LOG IN</span><span>BLOG</span></div>

  <div class="abs brand"><div class="brand-mark"></div><div class="brand-name">AshmoorMedical</div></div>
  <div class="abs tagline">Immediate Family and Personal Care</div>
  <div class="abs contact">CALL : (555) 201-4836
FAX   : (555) 201-4837</div>

  <nav class="abs mainnav">
    <span style="left:48px">HOME</span>
    <span style="left:109px">ABOUT</span>
    <span style="left:174px">SERVICES</span>
    <span style="left:238px">STAFF</span>
    <span style="left:307px">INSURANCE</span>
    <span style="left:379px">VIDEOS</span>
    <span style="left:446px">CONTACT</span>
  </nav>
  <div class="abs search">Search</div>
</header>

<section>
  <div class="abs slider" role="img" aria-label="Slider photo of a smiling family of parents, grandparents and children"></div>
  <div class="abs dot" style="left:99px"></div>
  <div class="abs dot" style="left:111px"></div>
  <div class="abs dot" style="left:123px"></div>
  <div class="abs dot on" style="left:135px"></div>
  <div class="abs dot" style="left:147px"></div>
  <div class="abs slide-title">CONCIERGE<br>CONVENIENCE</div>

  <div class="abs appt"><h3>APPOINTMENT REQUEST</h3></div>
  <div class="abs field" style="top:183px">Name*</div>
  <div class="abs field" style="top:212px">Phone*</div>
  <div class="abs field" style="top:239px">E-Mail*</div>
  <div class="abs label" style="top:265px">Best Time to reach me:</div>
  <div class="abs label" style="top:280px;left:557px"><span class="radio" style="background:#888"></span>Morning</div>
  <div class="abs label" style="top:280px;left:625px"><span class="radio"></span>Evening</div>
  <div class="abs label" style="top:294px">How do you heard about us</div>
  <div class="abs field" style="top:306px;height:18px">Search Engine</div>
  <div class="abs" style="left:686px;top:310px;width:10px;height:9px;border:1px solid #888;font-size:5px;text-align:center;line-height:7px">▾</div>
  <div class="abs field" style="top:329px;height:35px">Describe your needs</div>
  <div class="abs label" style="top:367px">Word Verificatrion</div>
  <div class="abs captcha">GHWR</div>
  <div class="abs field" style="top:379px;left:588px;width:110px;height:12px"></div>
  <div class="abs submit">SUBMIT</div>
  <div class="abs shadow"></div>
</section>

<section>
  <h2 class="abs heading" style="left:80px;top:456px">Categories</h2>
  <div class="abs cat" style="top:494px"><i>›</i><span>Immediate care</span></div>
  <div class="abs cat" style="top:520px"><i>›</i><span>Allergies</span></div>
  <div class="abs cat" style="top:546px"><i>›</i><span>Primary care</span></div>
  <div class="abs cat" style="top:572px"><i>›</i><span>Women's health</span></div>
  <div class="abs cat" style="top:598px"><i>›</i><span>Medical spa treatments</span></div>
  <div class="abs cat" style="top:624px"><i>›</i><span>Men's health</span></div>
  <div class="abs cat" style="top:650px;border:0"><i>›</i><span>Weight loss</span></div>
  <div class="abs more" style="left:151px;top:680px"></div>

  <h2 class="abs heading" style="left:248px;top:457px">Welcome to Ashmoor Medical</h2>
  <div class="abs photo" style="left:246px;top:483px;width:281px;height:105px;border:1px solid #ddd" role="img" aria-label="Photo of a family of four smiling together"></div>
  <p class="abs para" style="left:246px;top:599px;width:281px">Lanternvale Medical Center is a full service medical facility with in-house lab and X-ray. We are here to take care of your medical needs whether they be family practice, urgent care or occupational in nature. Our providers and staff are eager to assist patients in a friendly efficient manner.</p>
  <p class="abs para" style="left:246px;top:647px;width:281px">Lanternvale Medical Center's director is also the chief clinician and owner. Dr. Owen Tarrell's position as a clinician and director allows him to manage patients and be involved in the day to day operation of his practice. This means there is a continual staff emphasis on excellent patient care.</p>
  <div class="abs learn" style="left:479px;top:682px">learn more &gt;&gt;</div>

  <h2 class="abs heading" style="left:554px;top:456px">Videos</h2>
  <div class="abs photo" style="left:554px;top:484px;width:166px;height:104px;background:linear-gradient(135deg,#e9eef2,#c9d3dc 50%,#f2ede6)" role="img" aria-label="Video still of a doctor examining a young boy"></div>
  <svg class="abs" style="left:622px;top:522px" width="28" height="20" viewBox="0 0 28 20"><rect width="28" height="20" rx="4" fill="#222"/><path d="M11 5 L19 10 L11 15 Z" fill="#fff"/></svg>
  <div class="abs" style="left:554px;top:580px;width:166px;height:8px;background:#222"></div>
  <p class="abs para" style="left:554px;top:599px;width:166px">Lorem Ipsum is simply dummy text of the printing and typesetting industry. Lorem Ipsum has been the industry's standard dummy text ever since the 1500s, when an unknown printer took a galley of type and scrambled it to make a type specimen book. It has survived not only five centuries, but also the leap into electronic typesetting, remaining essentially unchanged.</p>
  <div class="abs learn" style="left:672px;top:682px">learn more &gt;&gt;</div>
</section>

<section>
  <h2 class="abs heading" style="left:80px;top:712px">Medical Services</h2>
  <div class="abs svc" style="top:748px">Family Medicine<b>›</b></div>
  <div class="abs svc" style="top:778px">Adult Men<b>›</b></div>
  <div class="abs svc" style="top:807px">Adult Women<b>›</b></div>
  <div class="abs svc" style="top:838px">Kids/Teens/School<b>›</b></div>
  <div class="abs svc" style="top:866px">Pediatric/Infant<b>›</b></div>
  <div class="abs sub" style="top:894px"><i>›</i><span>Pediatric Care</span></div>
  <div class="abs sub" style="top:923px"><i>›</i><span>Wellness Exams</span></div>
  <div class="abs svc" style="top:952px">Minor Emergency<b>›</b></div>
  <div class="abs more" style="left:151px;top:989px"></div>

  <h2 class="abs heading" style="left:247px;top:712px">Treatments</h2>
  <div class="abs treat-img photo" style="left:246px;background:linear-gradient(180deg,#a9cdec,#d8c3a8 70%,#8fb36a)" role="img" aria-label="Photo of a family playing outdoors"></div>
  <div class="abs treat-img photo" style="left:424px" role="img" aria-label="Photo of a doctor consulting an elderly patient"></div>
  <div class="abs treat-img photo" style="left:597px;background:linear-gradient(135deg,#9fb4c8,#c7cfd6 45%,#c8242c 60%,#b31e25)" role="img" aria-label="Photo of a hospital emergency sign"></div>

  <div class="abs treat" style="left:246px;top:798px;width:170px">
    <h4>FAMILY MEDICAL CARE</h4>
    <ul><li>Cough, Colds, Flu Shots &amp; Strep Throat</li><li>Sinus &amp; Allergy Issues</li><li>Back, Chest &amp; Abdominal Pain</li><li>Wellness Exams/ Preventative Care</li><li>Pediatric Care</li><li>Men's Screening Tests</li><li>Women's Health Screenings</li></ul>
  </div>
  <div class="abs treat" style="left:425px;top:798px;width:165px">
    <h4>ADDITIONAL SERVICES</h4>
    <ul><li>Travel Vaccinations/Immunizations</li><li>US Immigration (INS) Physical Exams</li><li>Occupational/Employment</li><li>Physical Exams</li><li>Drug Testing/Screening</li><li>Pregnancy, HIV &amp; STD Screening</li><li>Lacerations &amp; X-Rays</li><li>Minor Emergencies/ Urgent Care</li></ul>
  </div>
  <div class="abs treat" style="left:597px;top:798px;width:124px">
    <h4>MINOR EMRGENCY</h4>
    <ul><li>Urgent Care</li><li>Laceration Repair</li><li>Initial Fracture Diagnosis</li><li>Strains &amp; Sprains</li><li>X-Rays &amp; EKGs</li><li>Minor Foot Care</li></ul>
  </div>
</section>

<section>
  <h2 class="abs heading" style="left:80px;top:1021px">Partners</h2>
  <div class="abs badge"></div>

  <h2 class="abs heading" style="left:247px;top:1021px">Testimonials</h2>
  <div class="abs arrowbtn" style="left:694px">◂</div>
  <div class="abs arrowbtn" style="left:709px">▸</div>

  <div class="abs avatar" style="left:246px;top:1057px" role="img" aria-label="Client portrait placeholder"></div>
  <p class="abs quote" style="left:293px;top:1059px">"We are totally satisfied that we have met our business objectives with the use of the Nexacrm product"</p>
  <p class="abs who" style="left:293px;top:1095px"><b>Calvin R. Moss,</b><br>Vice President Harlow &amp; Moss</p>

  <div class="abs avatar" style="left:506px;top:1057px" role="img" aria-label="Client portrait placeholder"></div>
  <p class="abs quote" style="left:553px;top:1059px;width:168px;text-align:justify">"leads has given us a hand up, made our work easier, and the whole process easier for our clients"</p>
  <p class="abs who" style="left:553px;top:1095px"><b>Dana Whitfield,</b><br>IT Manager Stepline Inc</p>
</section>

<footer>
  <div class="abs footer"></div>
  <div class="abs copy">Copyright ©2012 ASHMOORMEDICAL - All rights reserved</div>
  <div class="abs flink" style="left:438px">Home</div>
  <div class="abs flink" style="left:467px">|</div>
  <div class="abs flink" style="left:480px">About Us</div>
  <div class="abs flink" style="left:519px">|</div>
  <div class="abs flink" style="left:532px">Terms&amp; Conditions</div>
  <div class="abs flink" style="left:603px">|</div>
  <div class="abs flink" style="left:615px">Privacy Policy</div>
  <div class="abs flink" style="left:671px">|</div>
  <div class="abs flink" style="left:685px">Contact Us</div>
  <div class="abs flink" style="left:739px">CS</div>
</footer>
</body>
</html>
```